Water ATM Card

Need a design for water ATM cards. Size of card is 3.375 x 2.125 inch
On the Front include the Cedar hollow Logo.
Bottom right corner should have Price $100
On the Back
This card is to be used to access water refills at any Cedar Hollow Water Vending Machines.
Please contact (869) 418 2930 or (869) 534 1276 or email clearflowbox@mailvista.example for any assistance or recharging of card.

```html
<!DOCTYPE html>
<html lang="en">
<head>
<meta charset="utf-8">
<title>Cedar Hollow Water Card</title>
<link href="https://fonts.googleapis.com/css2?family=Montserrat:wght@400;500;700&display=swap" rel="stylesheet">
<style>
  :root {
    --page-bg: #e6e7e9;
    --card-blue-light: #2c6aa6;
    --card-blue-dark: #2b3782;
    --brand-blue: #1d5fae;
    --band-blue: #2170b4;
    --band-blue-deep: #1a5aa0;
    --accent-green: #3aa53a;
    --ink: #1e2a3a;
    --white: #ffffff;
  }
  * { box-sizing: border-box; margin: 0; padding: 0; }
  html, body { width: 1200px; height: 900px; overflow: hidden; }
  body {
    background: var(--page-bg);
    font-family: "Montserrat", Arial, sans-serif;
    display: flex;
    flex-direction: column;
    align-items: center;
    justify-content: center;
    gap: 40px;
  }
  .card {
    position: relative;
    width: 620px;
    height: 390px;
    border-radius: 6px;
    overflow: hidden;
    box-shadow: 0 4px 14px rgba(0,0,0,0.18);
  }
  /* Back face */
  .card-back {
    background: linear-gradient(160deg, var(--card-blue-light) 0%, var(--card-blue-dark) 70%);
    color: var(--white);
    text-align: center;
  }
  .card-back .brand-name {
    position: absolute;
    top: 140px;
    left: 0;
    right: 0;
    font-size: 44px;
    font-weight: 700;
    letter-spacing: 1px;
    text-transform: uppercase;
  }
  .card-back .assist-note {
    position: absolute;
    bottom: 70px;
    left: 0;
    right: 0;
    font-size: 13px;
    font-weight: 400;
  }
  /* Front face */
  .card-front { background: var(--white); }
  .card-front .band { position: absolute; inset: 0; width: 100%; height: 100%; }
  .front-brand {
    position: absolute;
    left: 40px;
    top: 150px;
    display: flex;
    align-items: center;
    gap: 10px;
  }
  .front-brand .brand-dot {
    width: 16px; height: 16px; border-radius: 50%;
    background: var(--accent-green);
  }
  .front-brand .brand-name {
    font-size: 28px;
    font-weight: 700;
    color: var(--brand-blue);
    text-transform: uppercase;
    letter-spacing: 0.5px;
  }
  .contact-block {
    position: absolute;
    left: 340px;
    top: 50px;
    padding-left: 14px;
    border-left: 1.5px solid var(--brand-blue);
  }
  .contact-block .person-name {
    font-size: 20px;
    font-weight: 700;
    color: var(--brand-blue);
    text-transform: uppercase;
  }
  .contact-block .person-role {
    font-size: 12px;
    color: var(--ink);
    margin: 2px 0 10px 10px;
    text-transform: uppercase;
  }
  .contact-list { list-style: none; }
  .contact-list li {
    display: flex;
    align-items: center;
    gap: 8px;
    font-size: 12px;
    color: var(--ink);
    margin-bottom: 6px;
  }
  .contact-list li:last-child { margin-bottom: 0; }
  .contact-list svg { width: 12px; height: 12px; flex: none; fill: var(--brand-blue); }
  .price-tag {
    position: absolute;
    right: 30px;
    bottom: 34px;
    font-size: 30px;
    font-weight: 700;
    color: var(--accent-green);
  }
</style>
</head>
<body>

<section class="card card-back" aria-label="Card back">
  <div class="brand-name">Cedar Hollow</div>
  <p class="assist-note">for any assistance or recharging of card.</p>
</section>

<section class="card card-front" aria-label="Card front">
  <svg class="band" viewBox="0 0 620 390" preserveAspectRatio="none" aria-hidden="true">
    <defs>
      <linearGradient id="bandFill" x1="0" y1="1" x2="1" y2="0">
        <stop offset="0" stop-color="#1a5aa0"/>
        <stop offset="1" stop-color="#2170b4"/>
      </linearGradient>
    </defs>
    <path d="M0,322 Q380,302 620,218 L620,390 L0,390 Z" fill="url(#bandFill)"/>
    <path d="M130,306 Q420,288 600,212" fill="none" stroke="#3aa53a" stroke-width="2.5"/>
  </svg>

  <div class="front-brand">
    <span class="brand-dot"></span>
    <span class="brand-name">Cedar Hollow</span>
  </div>

  <div class="contact-block">
    <div class="person-name">Daren Pryce</div>
    <div class="person-role">Ower</div>
    <ul class="contact-list">
      <li><svg viewBox="0 0 24 24"><path d="M6.6 10.8a15 15 0 0 0 6.6 6.6l2.2-2.2c.3-.3.7-.4 1-.2 1.1.4 2.3.6 3.6.6.6 0 1 .4 1 1V20c0 .6-.4 1-1 1A17 17 0 0 1 3 4c0-.6.4-1 1-1h3.5c.6 0 1 .4 1 1 0 1.3.2 2.5.6 3.6.1.3 0 .7-.2 1z"/></svg>(869) 418 2930</li>
      <li><svg viewBox="0 0 24 24"><path d="M7 2h10a2 2 0 0 1 2 2v16a2 2 0 0 1-2 2H7a2 2 0 0 1-2-2V4a2 2 0 0 1 2-2zm0 3v13h10V5z"/></svg>(869) 534 1276</li>
      <li><svg viewBox="0 0 24 24"><path d="M2 5h20v14H2zm2 2v.5l8 5 8-5V7z"/></svg>clearflowbox@mailvista.example</li>
      <li><svg viewBox="0 0 24 24"><path d="M12 2a10 10 0 1 0 0 20 10 10 0 0 0 0-20zm0 2c.8 1.2 1.5 2.5 1.9 4h-3.8c.4-1.5 1.1-2.8 1.9-4zM4.3 14a8 8 0 0 1 0-4h3.4a16 16 0 0 0 0 4zm7.7 6c-.8-1.2-1.5-2.5-1.9-4h3.8c-.4 1.5-1.1 2.8-1.9 4zm2.3-6H9.7a14 14 0 0 1 0-4h4.6a14 14 0 0 1 0 4zm2-0a16 16 0 0 0 0-4h3.4a8 8 0 0 1 0 4z"/></svg>www.cedarhollowwater.example</li>
    </ul>
  </div>

  <div class="price-tag">Price $100</div>
</section>

</body>
</html>
```